Tech business card design

We need an amazing business card design for our new business 'Pexla' a marketing tech startup based in Sydney, Australia. We provide an online marketplace for businesses to search and buy advertising media, connect with service providers and learn more about marketing. We wish to communicate 'cool tech', reliability and professionalism and design based around our logo.

Target Market(s)

Business Owners

Contact Information for Business Card

Name
Position
Email Address
Website
Phone Number

Font styles to use
Other font styles liked:
• Avenir & Avenir Next

Colors

Designer to choose colors to be used in the design.

```html
<!DOCTYPE html>
<html lang="en">
<head>
<meta charset="utf-8">
<title>Pexla Business Card</title>
<link rel="stylesheet" href="https://fonts.googleapis.com/css2?family=Open+Sans:wght@400;700;800&display=swap">
<style>
  :root {
    --navy: #22264a;
    --lavender: #d9d9e6;
    --rule: #cfccdc;
    --backdrop: #e0dcdc;
    --white: #ffffff;
    --border: #6b6b70;
  }
  * { margin: 0; padding: 0; box-sizing: border-box; }
  html, body { width: 975px; height: 1200px; overflow: hidden; }
  body {
    background: var(--backdrop);
    font-family: "Open Sans", sans-serif;
    position: relative;
  }
  .card {
    position: absolute;
    left: 58px;
    width: 860px;
    height: 491px;
  }
  .card--front { top: 92px; background: var(--white); border: 1px solid var(--border); }
  .card--back { top: 631px; background: var(--navy); }

  .tab {
    position: absolute;
    left: 0;
    width: 351px;
    height: 115px;
    border-radius: 0 58px 58px 0;
  }
  .card--front .tab { top: 230px; left: -1px; background: var(--navy); }
  .card--back .tab { top: 188px; background: var(--lavender); }

  .brand {
    position: absolute;
    color: var(--white);
    font-weight: 800;
    line-height: 1;
    letter-spacing: -1px;
  }
  .card--front .brand { left: 52px; top: 12px; font-size: 84px; }
  .card--back .brand { right: 46px; top: 48px; font-size: 108px; }

  .rule { position: absolute; height: 4px; }
  .card--front .rule { left: 364px; right: 0; top: 285px; background: var(--rule); }
  .card--back .rule { left: 362px; right: 2px; top: 244px; height: 3px; background: var(--lavender); }

  .front-url {
    position: absolute;
    top: 420px;
    left: 0; right: 0;
    text-align: center;
    font-size: 27px;
    letter-spacing: 3.5px;
    color: var(--navy);
    padding-left: 0;
    transform: translateX(-3px);
  }

  .person { position: absolute; left: 56px; top: 26px; color: var(--navy); }
  .person__name { font-weight: 700; font-size: 28px; line-height: 1.2; }
  .person__role { font-size: 25px; line-height: 1.3; }

  .contacts { position: absolute; left: 56px; top: 354px; list-style: none; color: var(--white); }
  .contacts li { display: flex; align-items: center; gap: 8px; font-size: 21px; height: 33px; }
  .contacts svg { width: 22px; height: 22px; flex: none; }

  .address {
    position: absolute;
    right: 46px;
    top: 362px;
    text-align: right;
    color: var(--white);
    font-size: 27px;
    line-height: 37px;
  }
</style>
</head>
<body>
  <section class="card card--front">
    <div class="tab"><span class="brand">Pexla</span></div>
    <div class="rule"></div>
    <p class="front-url">www.pexla.com</p>
  </section>

  <section class="card card--back">
    <span class="brand">Pexla</span>
    <div class="tab">
      <div class="person">
        <p class="person__name">JOHN SMITH</p>
        <p class="person__role">Position</p>
      </div>
    </div>
    <div class="rule"></div>
    <ul class="contacts">
      <li>
        <svg viewBox="0 0 24 24" fill="none" stroke="#fff" stroke-width="1.8" aria-hidden="true">
          <circle cx="12" cy="12" r="10.5"/>
          <path d="M8.2 6.5l2 2.2-1.1 1.6c.8 1.8 2 3 3.7 3.8l1.6-1.1 2.2 2-1.3 1.8c-3.9-.6-7.6-4.3-8.3-8.3z" fill="#fff"/>
        </svg>
        012-345-6789
      </li>
      <li>
        <svg viewBox="0 0 24 24" aria-hidden="true">
          <rect x="2" y="5" width="20" height="14" fill="#fff"/>
          <path d="M2 5l10 8 10-8M2 19l7.5-7M22 19l-7.5-7" stroke="#22264a" stroke-width="1.6" fill="none"/>
        </svg>
        info@pexla.com
      </li>
      <li>
        <svg viewBox="0 0 24 24" fill="none" stroke="#fff" stroke-width="1.5" aria-hidden="true">
          <circle cx="12" cy="12" r="10"/>
          <ellipse cx="12" cy="12" rx="4.5" ry="10"/>
          <path d="M2 12h20M3.5 7h17M3.5 17h17M12 2v20"/>
        </svg>
        www.pexla.com
      </li>
    </ul>
    <p class="address">Street name City Name,<br>Zipcode,012345</p>
  </section>
</body>
</html>
```